My project benefits Military, First Responders, Police, Fire, and Educators.

Contact Information for Business Card

2 Sided appointment card. Visual side will have my head shot with "Brisk Lantern" in a bold graffic/text. I am picturing maybe the headshot applied to a filter that has a matrix effect where the picture is made up of data/numbers flowing vertically through the photo. I am of course open to other concepts as well. Side two will have contact info presented in an attractive visual complimenting the front.

```html
<!DOCTYPE html>
<html lang="en">
<head>
<meta charset="utf-8">
<title>Brisk Lantern – Appointment Card</title>
<link href="https://fonts.googleapis.com/css2?family=Open+Sans:wght@300;400;600&display=swap" rel="stylesheet">
<style>
  :root {
    --stage: #ebebea;
    --brand-green: #14ad73;
    --rule-green: #4cc9a3;
    --ink-grey: #555555;
    --ring-grey: #666666;
    --white: #ffffff;
    --photo-dark: #1c2433;
    --photo-mid: #8a7a6e;
    --photo-light: #e6dcd6;
    --ghost-light: #ecebea;
    --ghost-mid: #d9d6d3;
  }
  * { box-sizing: border-box; margin: 0; padding: 0; }
  html, body { width: 1200px; height: 900px; overflow: hidden; }
  body {
    background: var(--stage);
    font-family: "Open Sans", Arial, sans-serif;
    position: relative;
  }
  .card {
    position: absolute;
    display: flex;
    box-shadow: 0 6px 18px rgba(0,0,0,0.12);
    overflow: hidden;
  }
  /* Front */
  .card--front { left: 238px; top: 62px; width: 555px; height: 342px; }
  .headshot {
    width: 263px; height: 100%;
    background: linear-gradient(180deg, var(--photo-light) 0%, var(--photo-mid) 45%, var(--photo-dark) 80%);
  }
  .front-panel {
    flex: 1;
    background: var(--brand-green);
    color: var(--white);
    padding: 22px 0 0 29px;
    position: relative;
  }
  .brand-mark {
    display: flex; align-items: center; gap: 12px;
    height: 126px;
  }
  .brand-mark__dot { flex: none; }
  .brand-mark__name { font-size: 22px; font-weight: 600; letter-spacing: 0.3px; }
  .person { margin-top: 32px; }
  .person__name { font-size: 19px; font-weight: 600; line-height: 1.2; }
  .person__role { font-size: 14.5px; font-weight: 400; line-height: 1.3; }
  .contact { list-style: none; margin-top: 30px; font-size: 14.5px; line-height: 20px; }
  .contact li { display: flex; align-items: center; gap: 8px; }
  .contact svg { width: 12px; height: 12px; flex: none; }
  /* Back */
  .card--back { left: 459px; top: 518px; width: 559px; height: 343px; }
  .back-panel {
    width: 283px; height: 100%;
    background: var(--white);
    padding: 0 0 0 25px;
    position: relative;
  }
  .back-brand { text-align: center; width: 240px; margin-top: 37px; }
  .back-brand__ring { display: block; margin: 0 auto; }
  .back-brand__name {
    margin-top: 10px;
    font-size: 26px; font-weight: 300; letter-spacing: 0.5px;
    color: var(--brand-green);
    text-transform: uppercase;
    white-space: nowrap;
  }
  .appointment__label { margin-top: 22px; font-size: 17px; color: var(--brand-green); }
  .appointment__line { width: 213px; height: 1px; background: var(--rule-green); margin-top: 30px; }
  .appointment__line + .appointment__line { margin-top: 31px; }
  .appointment__note { margin-top: 10px; font-size: 14.5px; line-height: 1.4; color: var(--ink-grey); }
  .ghost-headshot {
    flex: 1;
    background: linear-gradient(180deg, var(--ghost-light) 0%, var(--ghost-mid) 60%, #c9c5c2 100%);
  }
</style>
</head>
<body>
  <section class="card card--front">
    <div class="headshot" role="img" aria-label="Headshot of the managing director in a dark suit and tie"></div>
    <div class="front-panel">
      <div class="brand-mark">
        <svg class="brand-mark__dot" width="22" height="22" viewBox="0 0 22 22"><circle cx="11" cy="11" r="9" fill="none" stroke="#ffffff" stroke-width="3"/></svg>
        <span class="brand-mark__name">Brisk Lantern</span>
      </div>
      <div class="person">
        <div class="person__name">Daniel Hartley</div>
        <div class="person__role">Managing Director</div>
      </div>
      <ul class="contact">
        <li>
          <svg viewBox="0 0 12 12"><path d="M2.5 1 L4.5 1 L5.2 3.6 L3.9 4.6 C4.6 6 5.9 7.3 7.4 8.1 L8.4 6.8 L11 7.5 L11 9.5 C11 10.3 10.3 11 9.5 11 C5 11 1 7 1 2.5 C1 1.7 1.7 1 2.5 1 Z" fill="#ffffff"/></svg>
          044-987 654 321
        </li>
        <li>
          <svg viewBox="0 0 12 12"><rect x="1" y="2.5" width="10" height="7" fill="#ffffff"/><path d="M1.3 2.8 L6 6.3 L10.7 2.8" fill="none" stroke="#14ad73" stroke-width="1"/></svg>
          hello@brisklantern.com
        </li>
        <li>
          <svg viewBox="0 0 12 12"><circle cx="6" cy="6" r="5" fill="#ffffff"/><path d="M1 6 H11 M6 1 C3.8 3.5 3.8 8.5 6 11 M6 1 C8.2 3.5 8.2 8.5 6 11" fill="none" stroke="#14ad73" stroke-width="0.8"/></svg>
          www.brisklantern.com
        </li>
      </ul>
    </div>
  </section>

  <section class="card card--back">
    <div class="back-panel">
      <div class="back-brand">
        <svg class="back-brand__ring" width="80" height="80" viewBox="0 0 80 80"><circle cx="40" cy="40" r="36" fill="none" stroke="#666666" stroke-width="6"/></svg>
        <div class="back-brand__name">Brisk Lantern</div>
      </div>
      <div class="appointment">
        <div class="appointment__label">Appointment</div>
        <div class="appointment__line"></div>
        <div class="appointment__line"></div>
        <p class="appointment__note">If unable to keep appointment,<br>kindly give 24hrs notice.</p>
      </div>
    </div>
    <div class="ghost-headshot" role="img" aria-label="Faded headshot of the managing director in a suit"></div>
  </section>
</body>
</html>
```